Awesome photographers card for an awesome new business

Double sided business card Black background and silver logo in middle on one side. Details on otherside. please keep it simple

Industry/Entity Type

Photographer

Contact Information for Business Card

Gerald Fenwick
0452817360
GeraldFenwickPhotography47@mailbox.test
www.GeraldFenwickPhotography.test.au
Instagram _Gerald_fenwick

Requirements
Must have
• My logo in Silver
• please use instagram logo instead of "Instagram"

```html
<!DOCTYPE html>
<html lang="en">
<head>
<meta charset="utf-8">
<title>Gerald Fenwick Photography – Business Card</title>
<link rel="stylesheet" href="https://fonts.googleapis.com/css2?family=Open+Sans:wght@400&family=Yellowtail&display=swap">
<style>
  :root {
    --page: #ffffff;
    --card: #0f0f0f;
    --frame: #dcdcdc;
    --silver: #bcbcbc;
    --text: #ececec;
  }
  * { box-sizing: border-box; margin: 0; padding: 0; }
  html, body {
    width: 1200px; height: 1200px; overflow: hidden;
    background: var(--page);
    font-family: "Open Sans", Arial, sans-serif;
  }
  .card {
    position: absolute; left: 150px; width: 900px; height: 540px;
    background: var(--card);
  }
  .card--front { top: 54px; }
  .card--back { top: 621px; }
  .card__frame {
    position: absolute; left: 44px; top: 46px; width: 812px; height: 450px;
    border: 5px solid var(--frame);
  }
  .brand {
    position: absolute; width: 280px; height: 280px; border-radius: 50%;
    border: 4px solid var(--silver);
    display: flex; flex-direction: column; align-items: center; justify-content: center;
    color: var(--silver); text-align: center;
    font-family: "Open Sans", Arial, sans-serif; font-weight: 400;
    font-size: 20px; letter-spacing: 5px; line-height: 1.6;
  }
  .card--front .brand { left: 70px; top: 130px; }
  .card--back .brand { left: 322px; top: 60px; }
  .signature {
    position: absolute; text-align: center; color: var(--text); white-space: nowrap;
  }
  .signature__name {
    display: block; font-family: "Yellowtail", cursive; font-size: 46px; line-height: 1;
  }
  .signature__role { display: block; font-size: 17px; margin-top: 4px; }
  .card--front .signature { left: 464px; width: 300px; top: 136px; }
  .card--back .signature { left: 306px; width: 300px; top: 376px; }
  .card--back .signature__name { font-size: 38px; }
  .card--back .signature__role { font-size: 15px; margin-top: 0; }
  .contacts { position: absolute; left: 438px; top: 288px; list-style: none; }
  .contacts li {
    display: flex; align-items: center; height: 49.6px;
    color: var(--text); font-size: 16px; white-space: nowrap;
  }
  .contacts svg { width: 38px; height: 38px; margin-right: 8px; flex: none; }
  .website {
    position: absolute; right: 66px; top: 457px;
    color: var(--text); font-size: 16px; white-space: nowrap;
  }
</style>
</head>
<body>
  <section class="card card--front">
    <div class="card__frame"></div>
    <div class="brand">GERALD<br>FENWICK<br>PHOTOGRAPHY</div>
    <div class="signature">
      <span class="signature__name">Gerald Fenwick</span>
      <span class="signature__role">Photographer</span>
    </div>
    <ul class="contacts">
      <li>
        <svg viewBox="0 0 40 40" fill="none" stroke="#ececec" stroke-width="2.5"><path d="M20 3 L36 12 L36 28 L20 37 L4 28 L4 12 Z"/><path d="M14 12 l4 0 l1 5 l-2 2 q2 4 5 5 l2 -2 l5 1 l0 4 q-10 1 -15 -11 Z" stroke-width="1.6"/></svg>
        0452817360
      </li>
      <li>
        <svg viewBox="0 0 40 40" fill="none" stroke="#ececec" stroke-width="2.5"><path d="M20 3 L36 12 L36 28 L20 37 L4 28 L4 12 Z"/><rect x="11" y="14" width="18" height="12" stroke-width="1.6"/><path d="M11 14 L20 21 L29 14" stroke-width="1.6"/></svg>
        GeraldFenwickPhotography47@mailbox.test
      </li>
      <li>
        <svg viewBox="0 0 40 40" fill="none" stroke="#ececec" stroke-width="2.5"><path d="M20 3 L36 12 L36 28 L20 37 L4 28 L4 12 Z"/><circle cx="20" cy="20" r="9" stroke-width="1.6"/><path d="M11 20 H29" stroke-width="1.6"/></svg>
        www.GeraldFenwickPhotography.test.au
      </li>
      <li>
        <svg viewBox="0 0 40 40" fill="none" stroke="#ececec" stroke-width="2.5"><path d="M20 3 L36 12 L36 28 L20 37 L4 28 L4 12 Z"/><rect x="13" y="13" width="14" height="14" stroke-width="1.6"/></svg>
        _Gerald_fenwick
      </li>
    </ul>
  </section>

  <section class="card card--back">
    <div class="card__frame"></div>
    <div class="brand">GERALD<br>FENWICK<br>PHOTOGRAPHY</div>
    <div class="signature">
      <span class="signature__name">Gerald Fenwick</span>
      <span class="signature__role">Photographer</span>
    </div>
    <div class="website">www.GeraldFenwickPhotography.test.au</div>
  </section>
</body>
</html>
```